Silverbrook Horizon Logo/Business Card

Project MUST include a logo with business card. See attached picture.

Logo is attached to brief but I'd like to add the tagline: "Find what lies beyond the things you know" Logo should also have an emblem that represents the Vortellan movie concept of red pill or blue pill (one in each hand). This emblem can be used with SilverBrook HoriZon or without.

Two sided card

Back can have the question mark logo that is attached

I'd like the background to be black.

On side have person's info:
Dorian Pelley
Trainer, Speaker, Author
p: 555-014-2297
e: d@silverbrookhorizon.example
www.silverbrookhorizon.example

Have find us on friendloop, quipstream (just logos)

Target Market(s)

People looking to know what they don't know, self development, personal growth

Industry/Entity Type

Movie

Requirements
Must have
• qr code
two sided

```html
<!DOCTYPE html>
<html lang="en">
<head>
<meta charset="utf-8">
<title>SilverBrook HoriZon — Business Card</title>
<link rel="stylesheet" href="https://fonts.googleapis.com/css2?family=Oswald:wght@600&family=Open+Sans:wght@400;700&family=Crimson+Text&display=swap">
<style>
  :root {
    --stage: #5a4636;
    --card-white: #ffffff;
    --ink-dark: #4a4a4c;
    --ink-name: #333333;
    --band-dark: #4d4d4f;
    --silver-light: #f4f4f4;
    --silver-mid: #cfcfcf;
    --accent-orange: #f26522;
    --art-dark: #1f1f1f;
    --label-white: #ffffff;
  }
  * { box-sizing: border-box; margin: 0; padding: 0; }
  html, body { width: 1200px; height: 810px; overflow: hidden; }
  body { background: var(--stage); position: relative; font-family: "Open Sans", sans-serif; }

  .card { position: absolute; width: 565px; height: 320px; border-radius: 16px; overflow: hidden; box-shadow: 0 4px 10px rgba(0,0,0,.35); }

  /* Front */
  .card-front { left: 275px; top: 61px; background: var(--card-white); }
  .brand { position: absolute; left: 27px; top: 26px; width: 300px; }
  .brand-name { font-family: "Oswald", sans-serif; font-weight: 600; color: var(--ink-dark); font-size: 50px; line-height: 58px; text-transform: uppercase; letter-spacing: -1px; }
  .brand-mark { position: absolute; left: 186px; top: 100px; width: 14px; height: 14px; border-radius: 50%; background: var(--accent-orange); }
  .tagline { position: absolute; left: 27px; top: 150px; font-family: "Crimson Text", serif; font-size: 11.5px; color: var(--ink-name); text-transform: uppercase; white-space: nowrap; }
  .divider { position: absolute; left: 345px; top: 23px; width: 1px; height: 148px; background: #dcdcdc; }
  .watermark-front { position: absolute; left: 410px; top: 10px; font-family: "Oswald", sans-serif; font-weight: 600; font-size: 46px; line-height: 50px; color: rgba(0,0,0,.05); text-transform: uppercase; writing-mode: vertical-rl; }
  .person { position: absolute; left: 360px; top: 102px; }
  .person-name { font-weight: 700; font-size: 19px; color: var(--ink-name); text-transform: uppercase; }
  .person-role { font-size: 12px; color: var(--ink-name); margin-top: 1px; }
  .band { position: absolute; left: 0; top: 0; }
  .contact { position: absolute; color: #fff; font-size: 12.5px; display: flex; align-items: center; gap: 7px; }
  .contact svg { width: 11px; height: 11px; }
  .contact-phone { left: 52px; top: 275px; }
  .contact-email { left: 52px; top: 295px; }
  .contact-web { left: 341px; top: 295px; }

  /* Backs */
  .card-back-silver { left: 9px; top: 430px; background: linear-gradient(90deg, var(--silver-mid) 0%, var(--silver-light) 35%, #ffffff 55%, #e2e2e2 100%); }
  .card-back-orange { left: 608px; top: 422px; background: var(--accent-orange); }
  .question-art { position: absolute; left: 11px; top: 80px; width: 149px; height: 166px; background: linear-gradient(160deg, #2c2c2c, var(--art-dark)); }
  .rule { position: absolute; left: 0; top: 254px; width: 370px; height: 1px; }
  .card-back-silver .rule { background: linear-gradient(90deg, #b5b5b5, rgba(181,181,181,0)); }
  .card-back-orange .rule { background: linear-gradient(90deg, rgba(255,255,255,.8), rgba(255,255,255,.2)); }
  .social { position: absolute; left: 415px; top: 205px; width: 120px; text-align: center; font-family: "Crimson Text", serif; }
  .social-title { font-size: 17px; color: var(--ink-name); margin-bottom: 8px; }
  .card-back-orange .social-title { color: #fff; }
  .social-list { list-style: none; display: flex; flex-direction: column; gap: 5px; align-items: flex-start; padding-left: 12px; font-family: "Open Sans", sans-serif; font-size: 13px; font-weight: 700; color: #2a6fb4; }
  .card-back-orange .social-list { color: #fff; }
  .social-list li { display: flex; align-items: center; gap: 6px; }
  .social-list li::before { content: ""; width: 12px; height: 12px; border-radius: 50%; background: currentColor; }
  .watermark-back { position: absolute; left: 325px; top: 28px; font-family: "Oswald", sans-serif; font-weight: 600; font-size: 40px; line-height: 44px; color: rgba(0,0,0,.08); text-transform: uppercase; text-align: right; width: 230px; }

  .option-label { position: absolute; font-size: 34px; color: var(--label-white); transform: translateX(-50%); }
  .option-label-1 { left: 262px; top: 755px; }
  .option-label-2 { left: 881px; top: 750px; }
</style>
</head>
<body>

<section class="card card-front" aria-label="Card front">
  <svg class="band" width="565" height="320" viewBox="0 0 565 320" aria-hidden="true">
    <defs>
      <linearGradient id="swoosh" x1="0" x2="1">
        <stop offset="0" stop-color="#ffffff" stop-opacity="0"/>
        <stop offset=".5" stop-color="#a8a8a8"/>
        <stop offset="1" stop-color="#d8d8d8"/>
      </linearGradient>
    </defs>
    <path d="M0,226 C160,196 330,196 430,222 C490,236 530,226 565,206 L565,222 C530,240 490,246 430,232 C330,206 160,204 0,234 Z" fill="url(#swoosh)"/>
    <path d="M0,236 C160,206 330,206 430,232 C490,246 530,238 565,222 L565,320 L0,320 Z" fill="var(--band-dark)"/>
  </svg>

  <div class="watermark-front" aria-hidden="true">HoriZon</div>

  <div class="brand">
    <p class="brand-name">SilverBrook<br>HoriZon</p>
    <span class="brand-mark"></span>
  </div>
  <p class="tagline">“Find what lies beyond the things you know”</p>

  <div class="divider"></div>

  <div class="person">
    <p class="person-name">Dorian Pelley</p>
    <p class="person-role">Trainer, Speaker, Author</p>
  </div>

  <p class="contact contact-phone">
    <svg viewBox="0 0 12 12" aria-hidden="true"><path d="M2.5 1 L4.5 1 L5 3.5 L3.8 4.3 C4.5 6 6 7.5 7.7 8.2 L8.5 7 L11 7.5 L11 9.5 C11 10.5 10 11 9 11 C5 10.5 1.5 7 1 3 C1 2 1.5 1 2.5 1 Z" fill="#fff"/></svg>
    555-014-2297
  </p>
  <p class="contact contact-email"><span aria-hidden="true">@</span> d@silverbrookhorizon.example</p>
  <p class="contact contact-web">
    <svg viewBox="0 0 12 12" aria-hidden="true"><circle cx="6" cy="6" r="5.5" fill="#fff"/><path d="M0.5 6 H11.5 M6 0.5 C3 3 3 9 6 11.5 M6 0.5 C9 3 9 9 6 11.5" stroke="var(--band-dark)" stroke-width=".8" fill="none"/></svg>
    www.silverbrookhorizon.example
  </p>
</section>

<section class="card card-back-silver" aria-label="Card back, option 1">
  <div class="question-art" role="img" aria-label="Question mark artwork made of words on a black background"></div>
  <div class="rule"></div>
  <div class="social">
    <p class="social-title">Find us on</p>
    <ul class="social-list"><li>friendloop</li><li>quipstream</li></ul>
  </div>
</section>

<section class="card card-back-orange" aria-label="Card back, option 2">
  <div class="watermark-back" aria-hidden="true">SilverBrook<br>HoriZon</div>
  <div class="question-art" role="img" aria-label="Question mark artwork made of words on a black background"></div>
  <div class="rule"></div>
  <div class="social">
    <p class="social-title">Find us on</p>
    <ul class="social-list"><li>friendloop</li><li>quipstream</li></ul>
  </div>
</section>

<p class="option-label option-label-1">Option 1</p>
<p class="option-label option-label-2">Option 2</p>

</body>
</html>
```